The design should look similar to the uploaded example to accommodate the information needed for a business card template. I would like to see the colors orange and charcoal grey incorporated along with the logo.The following should be on the back of the card SPECIALIZING IN NEW AND USED TIRES & WHEELS FOR:- Loaders- Skid Steers- Telehandlers- Boom Lifts- Forklifs and moreELIMINATING DOWNTIMEWheel Exchange Program for New & Used Foam Filled and Solid Rubber TiresSPECIALTY SERVICES- Foam Filling Tires- Largest Tire Press in SE- ONSITE Forklift Tire Press- Boom Truck Services - Rubber Tracks

Target Market(s)

New and Existing Customers

Industry/Entity Type

Business

Contact Information for Business Card

NAMEHEAVY DUTY TIRE, LLC8470 Belvedere RoadWest Palm Beach, FL 33411P: 844-HD-TIRESF: 561-431-6469C:E: W: WWW.GRANITERIMSUPPLY-EXAMPLE.COM

Font styles to use
Sans Serif

Colors
f37122
333333

Requirements
Must have
• The logo and the information indicated for the backside of the card
Nice to have
• Keep the orange and charcoal grey colors

```html
<!DOCTYPE html>
<html lang="en">
<head>
<meta charset="utf-8">
<title>Granite Rim Supply business card</title>
<link href="https://fonts.googleapis.com/css2?family=Open+Sans:wght@400;600;700&display=swap" rel="stylesheet">
<style>
:root{
  --orange:#f37122;
  --orange-card:#f58a45;
  --charcoal:#333333;
  --card-dark:#232323;
  --stage:#3a3633;
  --white:#ffffff;
  --soft:#e9e9e9;
}
*{box-sizing:border-box;margin:0;padding:0}
html,body{width:1200px;height:844px;overflow:hidden}
body{background:var(--stage);font-family:"Open Sans",sans-serif;position:relative}
.card{position:absolute;top:268px;width:540px;height:309px;box-shadow:0 10px 24px rgba(0,0,0,.45);overflow:hidden}
.card-front{left:45px;background:radial-gradient(circle at 30% 40%,#2c2c2c,var(--card-dark));}
.card-back{left:615px;background:var(--orange-card);color:var(--white);text-align:center;padding:40px 24px 0}
.brand-mark{position:absolute;left:50px;top:72px;width:166px;height:166px;border-radius:50%;background:var(--orange);
  display:flex;align-items:center;justify-content:center;text-align:center}
.brand-name{color:var(--charcoal);font-weight:700;font-size:27px;line-height:1.05;letter-spacing:.5px}
.divider{position:absolute;left:268px;top:60px;width:1px;height:190px;background:linear-gradient(var(--orange),transparent)}
.details{position:absolute;left:288px;top:58px;right:16px;color:var(--soft)}
.person{color:var(--orange);font-weight:600;font-size:18px;margin-bottom:6px}
.company{color:var(--orange);font-weight:600;font-size:13px;margin-bottom:2px}
.address{font-size:13px;line-height:1.45;margin-bottom:10px}
.contacts{list-style:none;font-size:12.5px;line-height:1.55}
.contacts li{display:flex;align-items:center;gap:9px;white-space:nowrap}
.contacts svg{width:11px;height:11px;fill:var(--orange);flex:none}
.back-heading{font-weight:700;font-size:15px;letter-spacing:.2px}
.back-line{font-size:13px;line-height:1.35}
.back-sub{font-weight:700;font-size:13px;margin-top:12px}
.back-section{font-weight:700;font-size:16px;margin-top:12px;margin-bottom:4px}
</style>
</head>
<body>
<section class="card card-front">
  <div class="brand-mark"><span class="brand-name">GRANITE<br>RIM</span></div>
  <div class="divider"></div>
  <div class="details">
    <p class="person">Daniel Reyes</p>
    <p class="company">GRANITE RIM SUPPLY, LLC</p>
    <p class="address">5126 Marston Lane<br>Cedar Bluff, FL 32990</p>
    <ul class="contacts">
      <li><svg viewBox="0 0 12 12"><path d="M2.5 0.5l2 2.3-1.1 1.5c.7 1.6 2 2.9 3.6 3.6l1.5-1.1 2.3 2-1.2 2.2C4.6 10.6 1.4 7.4.3 1.7z"/></svg>844-GR-WHEEL</li>
      <li><svg viewBox="0 0 12 12"><path d="M3 0h6v3H3zM1 4h10v6H9v2H3v-2H1zM4 8v3h4V8z"/></svg>561-278-9053</li>
      <li><svg viewBox="0 0 12 12"><path d="M3 0h6a1 1 0 0 1 1 1v10a1 1 0 0 1-1 1H3a1 1 0 0 1-1-1V1a1 1 0 0 1 1-1zm0 1.5V9.5h6V1.5z"/></svg>123-456-7890</li>
      <li><svg viewBox="0 0 12 12"><path d="M0 2h12v8H0zm1 1v.4l5 3.3 5-3.3V3z"/></svg>info@graniterim-example.com</li>
      <li><svg viewBox="0 0 12 12"><path d="M6 0a6 6 0 1 0 0 12A6 6 0 0 0 6 0zm0 1.2c.9 1 1.4 2.7 1.5 4.2h-3C4.6 3.9 5.1 2.2 6 1.2zM4.5 6.6h3c-.1 1.5-.6 3.2-1.5 4.2-.9-1-1.4-2.7-1.5-4.2z"/></svg>www.graniterimsupply-example.com</li>
    </ul>
  </div>
</section>

<section class="card card-back">
  <p class="back-heading">SPECIALIZING IN NEW AND USED TIRES &amp; WHEELS FOR</p>
  <p class="back-line">Loaders | Skid Steers | Telehandlers | Boom Lifts<br>Forklifs and more</p>
  <p class="back-sub">ELIMINATING DOWNTIME</p>
  <p class="back-line">Wheel Exchange Program for New &amp; Used Foam<br>Filled and Solid Rubber Tires</p>
  <p class="back-section">SPECIALTY SERVICES</p>
  <p class="back-line">Foam Filling Tires | Largest Tire Press in SE<br>ONSITE Forklift Tire Press | Boom Truck Services | Rubber Tracks</p>
</section>
</body>
</html>
```